Business card por a urban DJ, up scale audience target

Need a sober design, modern, conservative colors but i can consider some options, y play rnb, hip hop, EDM and top40.

Business card for contact and personal info, double sided, use logo attrached please; im 42 so i need a card acording to my age an target audience.

Target Market(s)

Adult people, up scale audience

Industry/Entity Type

Music Download

Contact Information for Business Card

Cel (318) 4207265518 www.lumadrift.com

Requirements
Must have
• open mind
Nice to have
• open mind
Should not have
• DJ

```html
<!DOCTYPE html>
<html lang="en">
<head>
<meta charset="utf-8">
<title>Lumadrift Business Card</title>
<link rel="stylesheet" href="https://fonts.googleapis.com/css2?family=Jost:wght@400;500;700&display=swap">
<style>
  :root {
    --backdrop: #34373b;
    --card-light: #fbfbfb;
    --card-dark: #1c1c1c;
    --ink: #1a1a1a;
    --ink-muted: #7a7a7a;
    --ink-soft: #444444;
    --paper-text: #f2f2f2;
  }
  * { margin: 0; padding: 0; box-sizing: border-box; }
  html, body {
    width: 1200px;
    height: 750px;
    overflow: hidden;
  }
  body {
    background: var(--backdrop);
    font-family: "Jost", "Century Gothic", sans-serif;
    position: relative;
  }
  .card {
    position: absolute;
    top: 228px;
    width: 461px;
    height: 262px;
  }
  .card--front { left: 124px; background: var(--card-light); color: var(--ink); }
  .card--back { left: 618px; background: var(--card-dark); color: var(--paper-text); }

  .brand {
    position: absolute;
    display: flex;
    align-items: center;
    gap: 8px;
    font-weight: 700;
    line-height: 1;
    letter-spacing: 2px;
  }
  .brand__square {
    display: block;
    background: currentColor;
  }
  .card--front .brand {
    right: 30px;
    top: 44px;
    font-size: 44px;
    color: var(--ink);
  }
  .card--front .brand__square { width: 14px; height: 14px; }

  .card--back .brand {
    left: 0;
    right: 0;
    top: 96px;
    justify-content: center;
    font-size: 56px;
  }
  .card--back .brand__square { width: 18px; height: 18px; }

  .holder {
    position: absolute;
    left: 30px;
    top: 156px;
  }
  .holder__name {
    font-size: 18px;
    font-weight: 500;
    letter-spacing: 0.2px;
  }
  .holder__role {
    font-size: 13px;
    color: var(--ink-muted);
    margin-top: 2px;
  }
  .contact {
    list-style: none;
    margin-top: 14px;
    font-size: 13px;
    color: var(--ink-soft);
  }
  .contact__item {
    display: flex;
    align-items: center;
    gap: 6px;
    height: 18px;
  }
  .contact__icon { width: 10px; height: 12px; flex: none; }

  .back-url {
    position: absolute;
    left: 0;
    right: 0;
    top: 182px;
    text-align: center;
    font-size: 11px;
    font-weight: 500;
    letter-spacing: 2px;
  }
</style>
</head>
<body>
  <section class="card card--front" aria-label="Card front">
    <div class="brand">
      <span class="brand__square"></span>
      <span class="brand__name">LUMA</span>
    </div>
    <div class="holder">
      <h1 class="holder__name">MARCUS HALE</h1>
      <p class="holder__role">CEO/FOUNDER</p>
      <ul class="contact">
        <li class="contact__item">
          <svg class="contact__icon" viewBox="0 0 10 14" aria-hidden="true">
            <rect x="1" y="0.8" width="8" height="12.4" rx="1.2" fill="none" stroke="#1a1a1a" stroke-width="1.5"/>
            <rect x="3.5" y="10.6" width="3" height="1" fill="#1a1a1a"/>
          </svg>
          <span>(318) 4207265518</span>
        </li>
        <li class="contact__item">
          <svg class="contact__icon" viewBox="0 0 12 12" aria-hidden="true">
            <circle cx="6" cy="6" r="5.5" fill="#1a1a1a"/>
            <path d="M3 3.5 Q5 4.5 4.5 6.5 Q6 8 5 10 M7.5 1.5 Q7 3.5 9 4 Q10 6 8.5 7.5" fill="none" stroke="#fbfbfb" stroke-width="1"/>
          </svg>
          <span>www.lumadrift.com</span>
        </li>
      </ul>
    </div>
  </section>

  <section class="card card--back" aria-label="Card back">
    <div class="brand">
      <span class="brand__square"></span>
      <span class="brand__name">LUMA</span>
    </div>
    <p class="back-url">WWW.LUMADRIFT.COM</p>
  </section>
</body>
</html>
```